RW Framewell Inc Business cards

We need business cards using our existing logo but slightly modified. Right now the logo says RW Loadbearing Masonry. We want to keep the RW part of the design, but replace the Structural Concrete portion with "FRAMEWELL". Please see the attached file.
Ideally this would be a blank template so we can add Different Names, titles, and phone numbers later.
On the one side we want only the logo and on the other side the detail. I'm attaching an example for you to see.
Please reach out with any other questions. Our address and other details will be given out once we find a design we like.

Target Market(s)

Construction Industry

```html
<!DOCTYPE html>
<html lang="en">
<head>
<meta charset="utf-8">
<title>RW Framewell Inc – Business Cards</title>
<link rel="stylesheet" href="https://fonts.googleapis.com/css2?family=Roboto:wght@400;500;700&display=swap">
<style>
  :root {
    --brand-blue: #1f75c0;
    --ink-grey: #6b6b6b;
    --text-dark: #333333;
    --card-white: #ffffff;
    --backdrop: #e9ebee;
  }
  * { margin: 0; padding: 0; box-sizing: border-box; }
  html, body { width: 1200px; height: 913px; overflow: hidden; }
  body {
    background: var(--backdrop);
    font-family: "Roboto", Arial, sans-serif;
    position: relative;
  }
  .card {
    position: absolute;
    left: 290px;
    width: 620px;
    height: 354px;
    border-radius: 3px;
    box-shadow: 0 6px 18px rgba(0,0,0,0.12);
  }
  .card--front { top: 60px; background: var(--brand-blue); color: var(--card-white); }
  .card--back { top: 474px; background: var(--card-white); color: var(--text-dark); }

  /* Front side */
  .front-wordmark {
    position: absolute;
    left: 0; right: 0; top: 120px;
    text-align: center;
    font-weight: 500;
    font-size: 52px;
    letter-spacing: 3px;
  }
  .front-web {
    position: absolute;
    left: 0; right: 0; top: 262px;
    text-align: center;
    font-size: 15px;
    letter-spacing: 0.5px;
  }

  /* Back side */
  .back-wordmark {
    position: absolute;
    right: 36px; top: 44px;
    color: var(--brand-blue);
    font-weight: 500;
    font-size: 36px;
    letter-spacing: 2px;
  }
  .edge-tab {
    position: absolute;
    left: -6px; top: 178px;
    width: 14px; height: 44px;
    border-radius: 6px;
    background: var(--brand-blue);
  }
  .contact {
    position: absolute;
    left: 60px; top: 170px;
  }
  .contact__name {
    color: var(--brand-blue);
    font-weight: 400;
    font-size: 27px;
    letter-spacing: 1.5px;
  }
  .contact__title {
    color: var(--ink-grey);
    font-size: 13px;
    letter-spacing: 1.5px;
    margin-top: 2px;
  }
  .contact__address {
    font-size: 13.5px;
    line-height: 1.4;
    margin: 12px 0 0 22px;
  }
  .contact__list { list-style: none; margin: 6px 0 0 22px; }
  .contact__item {
    display: flex; align-items: center; gap: 8px;
    font-size: 17px; line-height: 1.35;
  }
  .contact__icon { width: 15px; height: 15px; fill: var(--brand-blue); flex: none; }
</style>
</head>
<body>

<section class="card card--front" aria-label="Card front">
  <div class="front-wordmark">RW FRAMEWELL</div>
  <div class="front-web">www.rwframewell.com</div>
</section>

<section class="card card--back" aria-label="Card back">
  <div class="edge-tab"></div>
  <div class="back-wordmark">RW FRAMEWELL</div>

  <div class="contact">
    <h1 class="contact__name">DANIEL HARTWELL</h1>
    <p class="contact__title">DIRECTOR</p>
    <p class="contact__address">42 Ferrow Lane, Eastbank,<br>Harbour District (Exit B4)</p>
    <ul class="contact__list">
      <li class="contact__item">
        <svg class="contact__icon" viewBox="0 0 24 24" aria-hidden="true"><path d="M6.6 10.8a15.1 15.1 0 0 0 6.6 6.6l2.2-2.2a1 1 0 0 1 1-.25 11.4 11.4 0 0 0 3.6.6 1 1 0 0 1 1 1V20a1 1 0 0 1-1 1A17 17 0 0 1 3 4a1 1 0 0 1 1-1h3.5a1 1 0 0 1 1 1c0 1.25.2 2.45.6 3.6a1 1 0 0 1-.25 1z"/></svg>
        5550142870
      </li>
      <li class="contact__item">
        <svg class="contact__icon" viewBox="0 0 24 24" aria-hidden="true"><path d="M2 5h20v14H2z M3.5 6.5 12 13l8.5-6.5" fill="none" stroke="#1f75c0" stroke-width="2"/></svg>
        info@rwframewell.com
      </li>
      <li class="contact__item">
        <svg class="contact__icon" viewBox="0 0 24 24" aria-hidden="true"><circle cx="12" cy="12" r="10" fill="none" stroke="#1f75c0" stroke-width="2"/><path d="M2 12h20M12 2c3 3 3 17 0 20M12 2c-3 3-3 17 0 20" fill="none" stroke="#1f75c0" stroke-width="1.6"/></svg>
        www.rwframewell.com
      </li>
    </ul>
  </div>
</section>

</body>
</html>
```